Develop website for Cloud Security Startup

Looking for a logo that conveys the outsourced security and management of clients data, systems and development in Tellix, Bri and Pindle with an emphasis on security and compliance

Target Market(s)

Companies looking for professional services IT firm

Coding

Coded - Design and coding required

Number of Pages Required

5+ page

Font styles to use
Sans Serif

Colors
0455a3
33a6d7

Requirements
Must have
• Landing Page
- Help me get started

Move to the cloud safely
- Benefits of Cloud

What we do
- Cloud Adoption
- Managed Services
- Optimise

Resources
- News
- Resources
- Events
- Webinars
- Not for profit
- Case Studies
- Support Button
- Incident Button

Company
- About Us
- Why Vorplexa?
- Acreditations
- Quorvane Tellix Partner
- Net Promoter Score
- Careers
- Contact Us

Contact Us

```html
<!DOCTYPE html>
<html lang="en">
<head>
<meta charset="utf-8">
<title>Vorplexa — Cloud Security</title>
<link rel="stylesheet" href="https://fonts.googleapis.com/css2?family=Montserrat:wght@600;700&family=Lato:wght@400;700&display=swap">
<style>
:root{
  --navy:#0b1f6e;
  --navy-deep:#0a1650;
  --brand:#0455a3;
  --sky:#33a6d7;
  --bright:#1a7fd4;
  --ink:#111a2e;
  --muted:#6b7280;
  --mist:#e4ecf2;
  --white:#ffffff;
}
*{box-sizing:border-box;margin:0;padding:0}
html,body{width:1200px;height:3521px;overflow:hidden}
body{position:relative;background:var(--white);font-family:'Lato',sans-serif;color:var(--ink)}
.abs{position:absolute}
.heading{font-family:'Montserrat',sans-serif;font-weight:700;font-size:44px;letter-spacing:1px;text-align:center;left:0;width:1200px}
.heading .accent{color:var(--bright)}
.heading .strong{color:var(--navy)}

/* header */
.site-header{top:0;left:0;width:1200px;height:88px;background:var(--white);z-index:3}
.logo-disc{left:144px;top:-73px;width:248px;height:248px;border-radius:50%;background:var(--white);z-index:4}
.logo-mark{left:144px;top:80px;width:248px;text-align:center;z-index:5}
.logo-mark .dot{display:inline-block;width:18px;height:18px;border-radius:50%;background:var(--brand);margin-bottom:6px}
.logo-mark .name{font-family:'Lato',sans-serif;font-weight:700;font-size:28px;color:var(--navy);letter-spacing:2px;line-height:1}
.logo-mark .tag{font-family:'Lato',sans-serif;font-weight:700;font-size:8.5px;color:var(--navy);letter-spacing:.4px;margin-top:3px}
.nav{top:32px;left:0;z-index:5;font-size:16px;font-weight:700;color:var(--ink)}
.nav a{position:absolute;white-space:nowrap;color:inherit;text-decoration:none}
.nav a.active{color:var(--bright)}
.nav .pin-dot{position:absolute;left:-20px;top:3px;width:14px;height:14px;border-radius:50%;background:var(--brand)}

/* hero */
.hero-art{top:0;left:0}
.hero-visual{left:78px;top:194px;width:460px;height:460px;border-radius:50%;
  background:radial-gradient(circle at 50% 50%,#e6e8ec 0,#9aa2ad 24%,#15171c 30%,#0a0d14 56%,#0d4fb0 66%,#0a2a6a 74%,rgba(8,20,50,0) 76%)}
.hero-title{left:585px;top:268px;font-family:'Montserrat',sans-serif;font-weight:600;font-size:84px;color:var(--white);letter-spacing:3px;line-height:1}
.hero-sub{left:585px;top:374px;font-weight:700;font-size:20px;color:var(--white)}
.btn{display:flex;align-items:center;justify-content:center;border-radius:30px;background:var(--navy);color:var(--white);font-weight:700;font-size:16px;text-decoration:none}
.hero-btn{left:585px;top:439px;width:171px;height:57px;background:#0a1a5c}
.slider-dots{left:1137px;top:354px;width:8px}
.slider-dots span{display:block;width:8px;height:8px;border-radius:50%;background:var(--white);margin-bottom:9px}
.slider-dots span.on{background:var(--bright)}

/* benefits */
.benefit-text{font-size:18px;font-weight:700;line-height:28px;color:var(--ink)}
.benefit-text.left{text-align:right}
.benefit-icon{width:82px;height:82px;border-radius:50%;background:var(--navy);display:flex;align-items:center;justify-content:center}
.benefit-icon.light{background:var(--brand)}
.core-name{left:436px;top:1104px;width:280px;text-align:center;font-weight:700;font-size:30px;color:var(--navy);letter-spacing:2px}

/* what we do */
.service-card{width:291px;height:297px;border-radius:5px;overflow:hidden}
.service-card .label{position:absolute;left:0;bottom:38px;width:100%;text-align:center;color:var(--white);font-weight:700;font-size:20px}
.card-cloud{background:linear-gradient(180deg,#2f62c8 0%,#2a4fb0 55%,#0d1f7a 100%)}
.card-team{background:linear-gradient(180deg,#7a7670 0%,#4a5578 50%,#0d1f7a 100%)}
.card-opt{background:linear-gradient(180deg,#b08250 0%,#4b5f8a 45%,#0d1f7a 100%)}

/* about */
.about-title{left:158px;top:2134px;font-family:'Montserrat',sans-serif;font-weight:700;font-size:44px;letter-spacing:1px}
.about-copy{left:158px;top:2205px;width:430px;font-size:13px;line-height:24px;color:#4b5563}
.about-btn{left:158px;top:2422px;width:173px;height:58px}
.about-visual{left:646px;top:2122px;width:390px;height:390px;border-radius:50%;
  background:radial-gradient(circle at 40% 35%,#2a5fd0 0,#132a8a 45%,#0a1650 100%)}

/* resources */
.res-card{background:var(--white);border-radius:22px;overflow:hidden}
.res-img{position:absolute;border-radius:18px}
.res-date{font-size:13px;font-weight:700;color:var(--navy)}
.res-title{font-size:19px;font-weight:700;line-height:25px;color:var(--ink)}
.res-body{font-size:13px;line-height:22px;color:var(--muted)}
.res-more{font-size:16px;font-weight:700;color:var(--bright)}

/* footer */
.legal{left:141px;top:3473px;font-size:13px;color:var(--muted)}
.socials{top:3471px;left:880px;width:178px;text-align:right;font-size:14px;font-weight:700;color:#333}
.socials span{margin-left:10px}
</style>
</head>
<body>

<!-- hero background shapes -->
<svg class="abs hero-art" width="1200" height="780" viewBox="0 0 1200 780" aria-hidden="true">
  <defs>
    <linearGradient id="heroDark" x1="0" y1="0" x2="1" y2="0">
      <stop offset="0" stop-color="#0a2a6e"/>
      <stop offset=".45" stop-color="#06122e"/>
      <stop offset="1" stop-color="#020408"/>
    </linearGradient>
  </defs>
  <polygon points="0,554 335,770 1200,554" fill="var(--bright)"/>
  <polygon points="0,88 1200,88 1200,554 335,732 0,554" fill="url(#heroDark)"/>
</svg>

<div class="abs hero-visual" role="img" aria-label="Glowing digital ring around a silver cloud padlock emblem"></div>

<header class="abs site-header"></header>
<div class="abs logo-disc"></div>
<div class="abs logo-mark">
  <span class="dot"></span>
  <div class="name">VORPLEXA</div>
  <div class="tag">EFFECTIVE TECHNOLOGY MANAGEMENT</div>
</div>
<nav class="abs nav">
  <a class="active" style="left:472px"><span class="pin-dot"></span>Home</a>
  <a style="left:550px">Benefits</a>
  <a style="left:643px">What we do</a>
  <a style="left:763px">Resources</a>
  <a style="left:871px">Company</a>
  <a style="left:976px">Contact Us</a>
</nav>

<h1 class="abs hero-title">VORPLEXA</h1>
<p class="abs hero-sub">We are a cloud security startup outsourcing security</p>
<a class="abs btn hero-btn">GET STARTED</a>
<div class="abs slider-dots"><span></span><span></span><span></span><span class="on"></span><span></span></div>

<!-- benefits -->
<h2 class="abs heading" style="top:808px"><span class="accent">OUR</span> <span class="strong">BENEFITS</span></h2>

<svg class="abs" style="left:0;top:900px" width="1200" height="450" viewBox="0 900 1200 450" aria-hidden="true">
  <defs>
    <filter id="softShadow" x="-30%" y="-30%" width="160%" height="160%">
      <feDropShadow dx="0" dy="4" stdDeviation="8" flood-color="#000" flood-opacity=".15"/>
    </filter>
  </defs>
  <circle cx="576" cy="1119" r="174" fill="none" stroke="var(--brand)" stroke-width="3"/>
  <circle cx="576" cy="1119" r="137" fill="#fff" filter="url(#softShadow)"/>
  <g fill="#fff" stroke="var(--navy)" stroke-width="3">
    <circle cx="449" cy="1006" r="6"/><circle cx="705" cy="1006" r="6"/>
    <circle cx="403" cy="1117" r="6"/><circle cx="749" cy="1117" r="6"/>
    <circle cx="449" cy="1241" r="6"/><circle cx="703" cy="1241" r="6"/>
  </g>
</svg>
<div class="abs core-name">VORPLEXA</div>

<div class="abs benefit-text left" style="right:864px;top:946px">Lorem ipsum doloret<br>consectetdipisc</div>
<div class="abs benefit-icon light" style="left:349px;top:935px">
  <svg width="44" height="44" viewBox="0 0 44 44" fill="none" stroke="#fff" stroke-width="2.5"><circle cx="22" cy="10" r="4"/><circle cx="10" cy="24" r="4"/><circle cx="34" cy="24" r="4"/><circle cx="22" cy="34" r="4"/><path d="M4 34a6 6 0 0 1 12 0M28 34a6 6 0 0 1 12 0"/></svg>
</div>

<div class="abs benefit-text left" style="right:928px;top:1094px">Duis aute iruro<br>lorreprehenderit</div>
<div class="abs benefit-icon" style="left:279px;top:1085px">
  <svg width="44" height="44" viewBox="0 0 44 44" fill="none" stroke="#fff" stroke-width="2.5"><rect x="6" y="6" width="32" height="22"/><path d="M11 23l8-7 5 4 9-9M22 28v8M16 38l6-4 6 4"/></svg>
</div>

<div class="abs benefit-text left" style="right:860px;top:1257px">Sed ut perspiciatis<br>unde omnis</div>
<div class="abs benefit-icon light" style="left:354px;top:1234px">
  <svg width="44" height="44" viewBox="0 0 44 44" fill="none" stroke="#fff" stroke-width="2.2"><circle cx="22" cy="22" r="15"/><ellipse cx="22" cy="22" rx="7" ry="15"/><path d="M7 22h30M9 15h26M9 29h26"/></svg>
</div>

<div class="abs benefit-text" style="left:813px;top:946px">Nam libero temporecum<br>soluta nobis</div>
<div class="abs benefit-icon" style="left:720px;top:935px">
  <svg width="44" height="44" viewBox="0 0 44 44" fill="none" stroke="#fff" stroke-width="2.5"><path d="M10 34V24M16 34V20M22 34V16M28 34V22M6 20l10-8 8 5 12-10M30 7h6v6"/></svg>
</div>

<div class="abs benefit-text" style="left:858px;top:1094px">At vero eos et accusamus<br>et iusto gnlanditiis</div>
<div class="abs benefit-icon light" style="left:767px;top:1083px">
  <svg width="46" height="46" viewBox="0 0 46 46" fill="none" stroke="#fff" stroke-width="2.5"><circle cx="23" cy="23" r="19"/><path d="M14 23l6 6 12-12"/></svg>
</div>

<div class="abs benefit-text" style="left:817px;top:1257px">Ut enim ad minim<br>veniam liquip ex</div>
<div class="abs benefit-icon" style="left:720px;top:1234px">
  <svg width="44" height="44" viewBox="0 0 44 44" fill="none" stroke="#fff" stroke-width="2.5"><path d="M36 8c-10 0-18 6-22 16l6 6c10-4 16-12 16-22zM14 24l-6 2 4 4M20 30l-2 6-4-4M9 35l4-4"/><circle cx="27" cy="17" r="3"/></svg>
</div>

<!-- what we do -->
<svg class="abs" style="left:0;top:1390px" width="1200" height="660" viewBox="0 1390 1200 660" aria-hidden="true">
  <polygon points="0,1603 863,1390 1200,1603 1200,2050 0,2050" fill="var(--mist)"/>
</svg>
<h2 class="abs heading" style="top:1563px"><span class="accent">WHAT</span> <span class="strong">WE DO</span></h2>
<div class="abs service-card card-cloud" style="left:144px;top:1670px" role="img" aria-label="Hand touching a digital cloud network interface">
  <span class="label">Cloud Adoption</span></div>
<div class="abs service-card card-team" style="left:455px;top:1670px" role="img" aria-label="Support team with headsets working in an office">
  <span class="label">Managed Services</span></div>
<div class="abs service-card card-opt" style="left:766px;top:1670px" role="img" aria-label="Laptop with optimisation gear graphics overlay">
  <span class="label">Optimise</span></div>

<!-- about -->
<h2 class="abs about-title"><span style="color:var(--bright)">ABOUT</span> <span style="color:var(--navy)">US</span></h2>
<p class="abs about-copy">Lorem ipsum dolor sit amet, consectetur adipiscing elit, sed do eiusmod tempor incididunt ut labore et dolore magna aliquais ipsum suspendisse ultrices gravida. Risus commodo viverra maecenas accumsan lacus vel facilisis. Lorem ipsum dolor sit amet, consectetur adipiscing elit, sed do eiusmod tempor incididunt ut labore et dolore magna aliquais ipsum suspendisse ultrices gravida. Risus commodo viverra maecccumsan lacus vel facilisis. Lorem ipsum dolor sit amet, consectetur adipiscing elited do eiusmod temut labore et dolore magna</p>
<a class="abs btn about-btn">READ MORE</a>
<div class="abs about-visual" role="img" aria-label="Blue digital technology imagery representing secure cloud systems"></div>

<!-- resources -->
<svg class="abs" style="left:0;top:2529px" width="1200" height="906" viewBox="0 2529 1200 906" aria-hidden="true">
  <defs>
    <linearGradient id="resBlue" x1="0" y1="0" x2="0" y2="1">
      <stop offset="0" stop-color="#0c3596"/>
      <stop offset="1" stop-color="#1b62c4"/>
    </linearGradient>
  </defs>
  <polygon points="0,2741 864,2529 1200,2741 1200,3435 0,3435" fill="url(#resBlue)"/>
</svg>
<h2 class="abs heading" style="top:2710px;color:var(--white)">RESOURCES</h2>

<article class="abs res-card" style="left:141px;top:2819px;width:296px;height:507px">
  <div class="res-img" style="left:3px;top:3px;width:290px;height:222px;background:radial-gradient(circle at 50% 40%,#5fb6d8 0,#17506a 30%,#0a1a24 70%)" role="img" aria-label="Hand touching a glowing cloud padlock over dark circuitry"></div>
  <div class="abs res-date" style="left:23px;top:250px">Aug,2019</div>
  <div class="abs res-title" style="left:23px;top:282px;width:250px">Sed ut perspiciatis unde omnis iste natus</div>
  <div class="abs res-body" style="left:23px;top:348px;width:250px">Ut enim ad minima veniam, quis nos-treierci tationem ullam corporis suscipit laboriosan isi ut aliquid ex ea commodi eprehenderitq ui in ea voluptate velit .</div>
  <div class="abs res-more" style="left:23px;top:462px">READ MORE</div>
</article>

<article class="abs res-card" style="left:454px;top:2819px;width:605px;height:246px">
  <div class="res-img" style="left:2px;top:2px;width:237px;height:242px;background:linear-gradient(135deg,#6e7c5a 0%,#8a6a4a 35%,#2e4a72 70%,#1c2e4a 100%)" role="img" aria-label="Hands typing on a laptop with analytics chart overlay"></div>
  <div class="abs res-date" style="left:270px;top:27px">Aug,2019</div>
  <div class="abs res-title" style="left:270px;top:58px;width:270px">Sed ut perspiciatis unde omnis iste natus error</div>
  <div class="abs res-body" style="left:270px;top:117px;width:300px">Ut enim ad minima veniam, quis nostreierci tationem ullam corporis suscipit laboriosan isi ut aliquid ex ea eprehenderitq utate velit .</div>
  <div class="abs res-more" style="left:273px;top:201px">READ MORE</div>
</article>

<article class="abs res-card" style="left:454px;top:3080px;width:605px;height:246px">
  <div class="res-img" style="left:2px;top:2px;width:237px;height:242px;background:radial-gradient(circle at 50% 50%,#2f7ad8 0,#123a8a 55%,#0a1a4a 100%)" role="img" aria-label="Blue network of cloud data lines above a laptop"></div>
  <div class="abs res-date" style="left:270px;top:27px">Aug,2019</div>
  <div class="abs res-title" style="left:270px;top:58px;width:270px">Sed ut perspiciatis unde omnis iste natus error</div>
  <div class="abs res-body" style="left:270px;top:117px;width:300px">Ut enim ad minima veniam, quis nostreierci tationem ullam corporis suscipit laboriosan isi ut aliquid ex ea eprehenderitq utate velit .</div>
  <div class="abs res-more" style="left:273px;top:201px">READ MORE</div>
</article>

<!-- footer -->
<footer>
  <p class="abs legal">© 2021 Vorplexa.All Rights Reserved | &nbsp;Privacy policy &nbsp;| &nbsp;Terms and Conditions &nbsp;| Sitemap</p>
  <div class="abs socials"><span>Fenlo</span><span>Twirra</span><span>Linkora</span><span>Vidora</span></div>
</footer>

</body>
</html>
```